Willow Creek Gatherings Event Planning in need of a design!!

Event Planning company, does a variety of events. I like simple more rustic designs focused on almond blossoms. We are based out of Northern California, the heart of almond country. I would like to see colors in light pinks, beige, light browns, whites or creams. the final design should communicate rustic simplicity. Below are some pictures of Almond blossoms and design ideas I prefer the one called Tulip Grove. Thanks

Target Market(s)

Women in the mid twenties and older. They should be in the upper middle class in need of an amazing party design and coordinator

Industry/Entity Type

Event Planning

Contact Information for Business Card

Maren Lockwood 530-624-0295almondbaffairs@gmail.comalmondblossomaffairs.com

Font styles to use
Other font styles liked:
• Amatic SC

Requirements
Must have
• almond blossom
• my information
• simplicity
Nice to have
• rustic design
• vintage feel
• whimsical
Should not have
• i like pink but not over the top

```html
<!DOCTYPE html>
<html lang="en">
<head>
<meta charset="utf-8">
<title>Willow Creek Gatherings – Business Card</title>
<link rel="stylesheet" href="https://fonts.googleapis.com/css2?family=Jost:wght@400;500&family=Open+Sans:wght@400;600&display=swap">
<style>
  :root {
    --page-bg: #2b2b2b;
    --card-black: #121212;
    --card-black-edge: #1d1d1d;
    --gold: #a88660;
    --gold-soft: rgba(168,134,96,0.55);
    --white: #f4f1ec;
    --muted-line: #3a3a3a;
    --photo-dark: #2f332c;
    --photo-green: #4f5a45;
    --photo-branch: #5b4a40;
    --photo-blossom: #d9d2cc;
    --photo-pink: #c9a7a0;
  }
  * { box-sizing: border-box; margin: 0; padding: 0; }
  html, body {
    width: 1200px; height: 900px; overflow: hidden;
    background: var(--page-bg);
  }
  .canvas {
    width: 1200px; height: 900px;
    display: flex; align-items: center; justify-content: center; gap: 40px;
  }
  .card {
    position: relative;
    width: 540px; height: 309px;
    border-radius: 22px;
    overflow: hidden;
    background: linear-gradient(135deg, var(--card-black-edge), var(--card-black));
  }

  /* Front side */
  .brand-block {
    position: absolute; left: 30px; top: 0; bottom: 0; width: 260px;
    display: flex; flex-direction: column; justify-content: center; align-items: center;
    gap: 12px;
  }
  .ornament-area {
    width: 150px; height: 46px; border-radius: 23px;
    background: radial-gradient(ellipse at center, var(--gold-soft) 0%, rgba(168,134,96,0.15) 60%, transparent 100%);
  }
  .brand-name {
    font-family: "Jost", sans-serif; font-weight: 400;
    font-size: 27px; line-height: 1.25; letter-spacing: 2px;
    color: var(--gold); text-align: center;
  }
  .divider {
    position: absolute; left: 310px; top: 70px; bottom: 70px; width: 1px;
    background: var(--muted-line);
  }
  .contact-block {
    position: absolute; left: 330px; top: 96px;
    font-family: "Open Sans", sans-serif;
  }
  .contact-name {
    color: var(--gold); font-weight: 600; font-size: 16px; margin-bottom: 12px;
  }
  .contact-list { list-style: none; }
  .contact-item {
    display: flex; align-items: center; gap: 9px;
    color: var(--white); font-size: 12.5px; line-height: 1.7;
  }
  .contact-icon { width: 10px; height: 10px; flex: none; }

  /* Back side */
  .photo-fill {
    position: absolute; inset: 0;
    background:
      radial-gradient(ellipse 22% 26% at 70% 18%, var(--photo-blossom) 0%, transparent 100%),
      radial-gradient(ellipse 18% 22% at 88% 40%, var(--photo-blossom) 0%, transparent 100%),
      radial-gradient(ellipse 16% 20% at 30% 30%, var(--photo-pink) 0%, transparent 100%),
      radial-gradient(ellipse 14% 18% at 12% 78%, var(--photo-pink) 0%, transparent 100%),
      radial-gradient(ellipse 30% 30% at 40% 75%, var(--photo-branch) 0%, transparent 100%),
      linear-gradient(160deg, var(--photo-green), var(--photo-dark));
  }
  .photo-shade { position: absolute; inset: 0; background: rgba(18,18,18,0.42); }
  .back-brand-block {
    position: absolute; left: 0; right: 0; top: 62px;
    display: flex; flex-direction: column; align-items: center; gap: 12px;
  }
  .back-ornament-area {
    width: 150px; height: 46px; border-radius: 23px;
    background: radial-gradient(ellipse at center, rgba(244,241,236,0.5) 0%, rgba(244,241,236,0.12) 60%, transparent 100%);
  }
  .back-brand {
    font-family: "Jost", sans-serif; font-weight: 400;
    font-size: 30px; letter-spacing: 2px; color: var(--white);
  }
  .back-web {
    position: absolute; left: 0; right: 0; top: 232px;
    display: flex; align-items: center; justify-content: center; gap: 14px;
    font-family: "Open Sans", sans-serif; font-weight: 600;
    font-size: 13px; color: var(--white);
  }
  .back-web .rule { width: 70px; height: 1px; background: rgba(244,241,236,0.6); }
</style>
</head>
<body>
<main class="canvas">
  <section class="card card-front">
    <div class="brand-block">
      <div class="ornament-area" role="img" aria-label="Ornamental flourish above the company name"></div>
      <p class="brand-name">Willow Creek<br>Gatherings</p>
    </div>
    <div class="divider"></div>
    <div class="contact-block">
      <p class="contact-name">Maren Lockwood</p>
      <ul class="contact-list">
        <li class="contact-item">
          <svg class="contact-icon" viewBox="0 0 10 10"><rect x="2.5" y="0.5" width="5" height="9" rx="1" fill="none" stroke="#f4f1ec"/></svg>
          530-817-4362
        </li>
        <li class="contact-item">
          <svg class="contact-icon" viewBox="0 0 10 10"><rect x="0.5" y="2" width="9" height="6" fill="none" stroke="#f4f1ec"/><path d="M0.5 2 L5 5.5 L9.5 2" fill="none" stroke="#f4f1ec"/></svg>
          willowcgather@mailbox.test
        </li>
        <li class="contact-item">
          <svg class="contact-icon" viewBox="0 0 10 10"><circle cx="5" cy="5" r="4.5" fill="none" stroke="#f4f1ec"/><path d="M0.5 5 H9.5 M5 0.5 C2.5 3 2.5 7 5 9.5 M5 0.5 C7.5 3 7.5 7 5 9.5" fill="none" stroke="#f4f1ec" stroke-width="0.7"/></svg>
          willowcreekgatherings.test
        </li>
      </ul>
    </div>
  </section>

  <section class="card card-back">
    <div class="photo-fill" role="img" aria-label="Photograph of white and pale pink almond blossoms on a branch"></div>
    <div class="photo-shade"></div>
    <div class="back-brand-block">
      <div class="back-ornament-area" role="img" aria-label="Ornamental flourish above the company name"></div>
      <p class="back-brand">Willow Creek Gatherings</p>
    </div>
    <div class="back-web">
      <span class="rule"></span>
      <span>www.willowcreekgatherings.test</span>
      <span class="rule"></span>
    </div>
  </section>
</main>
</body>
</html>
```